Designing a brochures for an educational counseling service provider

We would like a 4 sided design on a 11x8.5 paper, half folded. I have including a sample design we did to give you an idea of what we envision but we welcome creativity to make beautiful looking flyers. Text for the flier is included as well as our logo.
- The most important thing is capturing our audience/market. We will be handing these flies to schools, organizations and individual clients.

www.pvrlearningadvisors.example

Target Market(s)

We are targeting international students wanting to study in the U.S and Canada.

Industry/Entity Type

Education

Requirements
Must have
• - Clean and clear
• - Our logo should visible and well placed.
• - Could you the pictures of students, libraries and school buildings or you could use the pictures we already have.
Nice to have
• We would like this to match business cards.

```html
<!DOCTYPE html>
<html lang="en">
<head>
<meta charset="utf-8">
<title>Educational Consulting Brochure – Inner Spread</title>
<link href="https://fonts.googleapis.com/css2?family=Raleway:wght@400;500;600;700&family=Open+Sans:ital,wght@0,700;1,700&display=swap" rel="stylesheet">
<style>
  :root {
    --green-dark: #1f9e3f;
    --green-light: #8ccc3c;
    --navy: #27337f;
    --blue: #1f72c0;
    --ink: #2f3033;
    --paper: #ffffff;
    --stage: #ecedef;
    --photo-warm-a: #6b4a3a;
    --photo-warm-b: #c9a889;
    --photo-lib-a: #1d2230;
    --photo-lib-b: #b9c1cb;
    --photo-field-a: #c9b08a;
    --photo-field-b: #e8e2d4;
    --bullet: #2b5fb3;
  }
  * { box-sizing: border-box; margin: 0; padding: 0; }
  html, body { width: 1200px; height: 900px; overflow: hidden; }
  body {
    background: var(--stage);
    font-family: "Raleway", "Helvetica Neue", Arial, sans-serif;
    color: var(--ink);
  }
  .spread {
    position: absolute;
    left: 70px; top: 40px;
    width: 1060px; height: 820px;
    display: flex;
    box-shadow: 0 10px 30px rgba(0,0,0,.18);
  }
  .page {
    position: relative;
    width: 530px; height: 820px;
    background: var(--paper);
    overflow: hidden;
  }
  .page--left { border-right: 1px solid #e3e3e3; }

  .tab {
    position: absolute;
    height: 46px;
    display: flex; align-items: center; justify-content: center;
    background: linear-gradient(90deg, var(--green-dark), var(--green-light));
    color: #fff;
    font-family: "Open Sans", Arial, sans-serif;
    font-weight: 700;
    font-size: 19px;
  }
  .tab--about { left: 0; top: 0; width: 130px; }
  .tab--services { left: 0; top: 18px; width: 118px; }
  .tab--small {
    height: 26px;
    width: 150px;
    left: 24px;
    font-size: 14px;
    justify-content: flex-start;
    padding-left: 10px;
  }
  .tab--boarding { top: 392px; }
  .tab--college { top: 536px; }

  .photo { position: absolute; }
  .photo--students-library {
    left: 136px; top: 0; width: 394px; height: 150px;
    background: linear-gradient(120deg, var(--photo-warm-a), var(--photo-warm-b) 60%, #3b3a3e);
  }
  .photo--library-stairs {
    left: 0; top: 480px; width: 530px; height: 262px;
    background: linear-gradient(110deg, var(--photo-lib-a) 0%, #3c4352 35%, var(--photo-lib-b) 70%, #e7ebef 100%);
  }
  .photo--students-field {
    left: 122px; top: 0; width: 408px; height: 150px;
    background: linear-gradient(110deg, var(--photo-field-a), var(--photo-field-b) 55%, #9c7a5e);
  }

  .copy {
    position: absolute;
    left: 24px; right: 24px;
    font-size: 12.6px;
    line-height: 1.36;
    text-align: justify;
  }
  .copy p + p { margin-top: 3px; }

  .about-copy { top: 166px; }

  .quote-band {
    position: absolute;
    left: 0; top: 396px; width: 530px; height: 84px;
    background: linear-gradient(90deg, var(--navy), var(--blue));
    color: #fff;
    display: flex; align-items: center; justify-content: center;
    text-align: center;
    padding: 0 40px;
    font-family: "Open Sans", Arial, sans-serif;
    font-style: italic;
    font-weight: 700;
    font-size: 16px;
    line-height: 1.3;
  }

  .foot-band {
    position: absolute;
    left: 0; top: 752px; width: 100%; height: 28px;
    background: linear-gradient(90deg, var(--green-dark), var(--green-light));
  }

  .services-intro { top: 162px; }
  .package-list { list-style: none; margin-top: 4px; }
  .package-list li { position: relative; padding-left: 14px; }
  .package-list li::before {
    content: ""; position: absolute; left: 0; top: 5px;
    width: 7px; height: 7px; background: var(--bullet);
  }
  .boarding-copy { top: 424px; }
  .college-copy { top: 568px; }
</style>
</head>
<body>
  <main class="spread">
    <section class="page page--left">
      <div class="tab tab--about">About Us</div>
      <div class="photo photo--students-library" role="img" aria-label="Photo of students studying together in a library"></div>

      <div class="copy about-copy">
        <p>Our mission is to make quality education accessible and affordable to the families we serve. Our services are designed with the child's future in mind. Whether one is seeking an academic or non-academic environment, it is important to us that we set our clients up for success.</p>
        <p>We are a family-centered organization and our goals are the same as those of our clients: for their child to thrive and reach their goals and dreams. With over 10 years of experience in the business, we are aware of the financial obstacles created by the ever increasing cost in education. Our expert consultants work closely with families to map out their educational budget and find the best affordable and quality educational options.</p>
      </div>

      <blockquote class="quote-band">“We offer comprehensive services to families, students, institutions and governmental organizations.”</blockquote>

      <div class="photo photo--library-stairs" role="img" aria-label="Photo of a curved library staircase lined with bookshelves"></div>

      <div class="foot-band"></div>
    </section>

    <section class="page page--right">
      <div class="photo photo--students-field" role="img" aria-label="Photo of smiling students standing outdoors on a sports field"></div>
      <div class="tab tab--services">Services</div>

      <div class="copy services-intro">
        <p>Finding the right school or program for your child is one of the most important decisions your family will make. The right choice will make a major impact on your child's future.</p>
        <p>Our package includes</p>
        <ul class="package-list">
          <li>Intake interview</li>
          <li>Present range of options based on needs and goals of the family</li>
          <li>Interview coaching</li>
          <li>Assistance with application and essays</li>
          <li>Updates on student progress throughout their enrollment with the school.</li>
          <li>Advisement on financial documents and visa applications</li>
        </ul>
      </div>

      <div class="tab tab--small tab--boarding">Boarding schools</div>
      <div class="copy boarding-copy">
        <p>Students who want the best out of their grade school experience are likely to choose boarding schools because they are proven to better prepare students for university. North American boarding schools provide a quality dynamic experience that will facilitate personal growth in independence, leadership, and confidence as well as provide the academic curriculum necessary to prepare students for university.</p>
      </div>

      <div class="tab tab--small tab--college">College admission:</div>
      <div class="copy college-copy">
        <p>As Educational Consultants, we specialize in college/university admissions and we understand how confusing, time-consuming, and stressful the application process can be. Our experienced counselors are here to answer your questions and guide you step by step. As parents and students may have limited access to information on schools, may not know or understand the entire process as a whole, nor where/how to begin, our experts counselors have a solutions.</p>
        <p>Clients increase the odds of admissions with our comprehensive plan of action. We believe that regardless of a student's level of involvement in extra-curricular activities or preparedness, they still possess something they can offer to the university, therefore we help them shine on their college applications.</p>
      </div>

      <div class="foot-band"></div>
    </section>
  </main>
</body>
</html>
```